Automotive eCommerce Business looking for a business card design

Looking for a clean and simple business card design. Our company name is "Brindle Auto" and we are a company specializing in the ecommerce sales of automotive parts, specifically for pick up trucks and large SUVs. Our company colours are red, black, and white.

Feel free to use the logo provided or create a new logo that you seem fit. Looking forward to your creative ideas!

Industry/Entity Type

Automotive

Contact Information for Business Card

We were thinking of a possibly two-sided design featuring just the logo and company name on one side, and personal information on the other side. Single sided designs will be considered as well.

Font styles to use
Serif
Sans Serif
Decorative

Colors
ec1f27
ffffff
000000

Requirements
Must have
• Space for employee's name, title, phone number and email address, along with the company address and website somewhere.

```html
<!DOCTYPE html>
<html lang="en">
<head>
<meta charset="utf-8">
<title>Brindle Auto – Business Card</title>
<link href="https://fonts.googleapis.com/css2?family=Cinzel:wght@400;500&family=Roboto:wght@400&display=swap" rel="stylesheet">
<style>
  :root {
    --backdrop: #1f1f20;
    --card-white: #f2f2f2;
    --brand-red: #9b1c20;
    --band-grey: #4a4e50;
    --back-grey: #4d5152;
    --ink-dark: #3a3a3a;
    --ink-light: #ffffff;
    --title-tint: #ecd3d3;
  }
  * { margin: 0; padding: 0; box-sizing: border-box; }
  html, body { width: 1200px; height: 960px; overflow: hidden; }
  body { background: var(--backdrop); position: relative; font-family: "Roboto", Arial, sans-serif; }

  .card { position: absolute; width: 600px; height: 342px; overflow: hidden; box-shadow: 0 2px 6px rgba(0,0,0,.5); }
  .card-front { left: 314px; top: 113px; background: var(--card-white); }
  .card-back { left: 311px; top: 472px; background: var(--back-grey); }

  .front-bands { position: absolute; inset: 0; }

  .brand-mark { position: absolute; left: 78px; top: 42px; width: 90px; height: 90px; background: var(--brand-red); border-radius: 4px; }
  .brand-name { position: absolute; left: 30px; top: 150px; font-family: "Cinzel", Georgia, serif; font-size: 21px; color: var(--ink-dark); letter-spacing: .2px; white-space: nowrap; }

  .contact-list { position: absolute; left: 36px; top: 243px; list-style: none; color: var(--ink-light); font-size: 14.5px; }
  .contact-list li { height: 19.3px; display: flex; align-items: center; gap: 8px; }
  .contact-list svg { width: 14px; height: 14px; fill: var(--ink-light); flex: none; }

  .person { position: absolute; right: 36px; top: 198px; text-align: right; font-family: "Cinzel", Georgia, serif; }
  .person-name { font-size: 22px; color: var(--ink-light); line-height: 26px; }
  .person-title { font-size: 16px; color: var(--title-tint); line-height: 20px; }

  .company-details { position: absolute; right: 36px; top: 261px; text-align: right; color: var(--ink-light); font-size: 14.5px; line-height: 19.5px; }
  .company-details .web { margin-top: 1px; }

  .back-name { position: absolute; right: 29px; top: 262px; font-family: "Cinzel", Georgia, serif; font-weight: 500; font-size: 23px; color: var(--ink-light); letter-spacing: .5px; }
  .back-web { position: absolute; right: 29px; top: 290px; font-size: 13.5px; color: var(--ink-light); letter-spacing: 3.6px; }
</style>
</head>
<body>

<section class="card card-front" aria-label="Business card front">
  <svg class="front-bands" viewBox="0 0 600 342" width="600" height="342" aria-hidden="true">
    <path d="M0 207 H328 L320 223 H0 Z" fill="var(--band-grey)"/>
    <path d="M0 225 H322 Q330 225 334 218 L350 190 Q356 180 368 180 H600 V342 H0 Z" fill="var(--card-white)"/>
    <path d="M0 227 H324 Q332 227 336 220 L352 192 Q358 182 370 182 H600 V342 H0 Z" fill="var(--brand-red)"/>
  </svg>

  <div class="brand-mark" aria-hidden="true"></div>
  <div class="brand-name">Brindle Auto Ltd.</div>

  <ul class="contact-list">
    <li><svg viewBox="0 0 24 24" aria-label="Phone"><path d="M6.6 10.8a15.1 15.1 0 0 0 6.6 6.6l2.2-2.2c.3-.3.7-.4 1-.2 1.1.4 2.3.6 3.6.6.6 0 1 .4 1 1V20c0 .6-.4 1-1 1A17 17 0 0 1 3 4c0-.6.4-1 1-1h3.5c.6 0 1 .4 1 1 0 1.3.2 2.5.6 3.6.1.3 0 .7-.2 1z"/></svg>604 218 7731</li>
    <li><svg viewBox="0 0 24 24" aria-label="Mobile"><path d="M7 1h10a2 2 0 0 1 2 2v18a2 2 0 0 1-2 2H7a2 2 0 0 1-2-2V3a2 2 0 0 1 2-2zm0 3v14h10V4zm5 15.5a1 1 0 1 0 0 2 1 1 0 0 0 0-2z"/></svg>604 552 9180</li>
    <li><svg viewBox="0 0 24 24" aria-label="Fax"><path d="M6 2h12v5H6zM3 8h18a2 2 0 0 1 2 2v7h-4v-3H5v3H1v-7a2 2 0 0 1 2-2zm3 7h12v7H6z"/></svg>604 317 4426</li>
    <li><svg viewBox="0 0 24 24" aria-label="Email"><path d="M2 5h20v2l-10 6L2 7zm0 4 10 6 10-6v10H2z"/></svg>parts@brindleauto.com</li>
  </ul>

  <div class="person">
    <div class="person-name">Marcus Hale</div>
    <div class="person-title">CEO/Founder</div>
  </div>

  <div class="company-details">
    <div>418 Copperline Road</div>
    <div>Ridgeford, Alaska 34518</div>
    <div class="web">www.brindleauto.com</div>
  </div>
</section>

<section class="card card-back" aria-label="Business card back">
  <div class="back-name">BRINDLE AUTO LTD</div>
  <div class="back-web">www.brindleauto.com</div>
</section>

</body>
</html>
```